Harborline Auto LLC

Car Dealer Customer Service
Address: 2874 Cresthaven Road, Larkwood Falls, ZZ 00000
web: www.harborlineautoxq.net
email: harborlineautoxq@mailnest.example
Phone: (931) 555-0148
Phone: (629) 555-0173

```html
<!DOCTYPE html>
<html lang="en">
<head>
<meta charset="utf-8">
<title>Harborline Auto – Business Card</title>
<link rel="stylesheet" href="https://fonts.googleapis.com/css2?family=Montserrat:wght@700&family=Poppins:wght@400;600&display=swap">
<style>
  :root {
    --backdrop: #2c2c2e;
    --card: #232325;
    --card-light: #2a2a2d;
    --blue: #2a8ac4;
    --gold: #e3a93b;
    --text: #e4e4e4;
    --emboss: #1a1a1b;
  }
  * { box-sizing: border-box; margin: 0; padding: 0; }
  html, body {
    width: 1200px; height: 1138px; overflow: hidden;
    background: var(--backdrop);
    font-family: "Poppins", sans-serif;
  }
  .card {
    position: absolute;
    width: 620px; height: 376px;
    border-radius: 16px;
    background: linear-gradient(160deg, var(--card-light), var(--card));
    box-shadow: 0 6px 14px rgba(0,0,0,.45);
    overflow: hidden;
  }
  .card--front { left: 274px; top: 186px; }
  .card--back { left: 275px; top: 606px; }

  /* front */
  .front-mark {
    position: absolute; left: 0; right: 0; top: 150px;
    display: flex; align-items: center; justify-content: center; gap: 14px;
  }
  .front-mark__dot {
    width: 30px; height: 30px; border-radius: 50%;
    background: var(--emboss);
  }
  .front-mark__name {
    font-family: "Montserrat", sans-serif; font-weight: 700;
    font-size: 40px; color: var(--emboss); letter-spacing: 1px;
  }
  .front-web {
    position: absolute; left: 0; right: 0; top: 334px;
    display: flex; align-items: center; justify-content: center; gap: 20px;
    font-size: 15px; color: var(--text);
  }
  .front-web__rule { width: 52px; height: 2px; background: var(--gold); }

  /* back */
  .emblem-area {
    position: absolute; left: -80px; top: 20px;
    width: 340px; height: 340px; border-radius: 50%;
    background: linear-gradient(180deg, #2a8ac4, #1f74ad);
  }
  .back-info {
    position: absolute; right: 26px; top: 0;
    text-align: right;
  }
  .brand-name {
    position: absolute; right: 0; top: 48px; white-space: nowrap;
    font-family: "Montserrat", sans-serif; font-weight: 700;
    font-size: 30px; line-height: 36px; color: var(--blue);
  }
  .person { position: absolute; right: 0; top: 150px; white-space: nowrap; }
  .person__name { font-weight: 600; font-size: 24px; color: var(--blue); line-height: 28px; }
  .person__role { font-size: 16px; color: var(--text); line-height: 22px; }
  .contacts { position: absolute; right: 0; top: 230px; white-space: nowrap; }
  .contact {
    display: flex; align-items: center; justify-content: flex-end; gap: 10px;
    font-size: 16px; line-height: 23px; color: var(--text);
  }
  .contact--phone { font-weight: 600; color: var(--blue); font-size: 17px; }
  .contact svg { width: 14px; height: 14px; fill: var(--gold); flex: none; }
  .contact--address { margin-top: 3px; }
</style>
</head>
<body>

<section class="card card--front">
  <div class="front-mark">
    <span class="front-mark__dot"></span>
    <span class="front-mark__name">HARBORLINE AUTO</span>
  </div>
  <div class="front-web">
    <span class="front-web__rule"></span>
    <span>www.harborlineautoxq.net</span>
    <span class="front-web__rule"></span>
  </div>
</section>

<section class="card card--back">
  <div class="emblem-area" role="img" aria-label="Brand emblem area"></div>
  <div class="back-info">
    <h1 class="brand-name">HARBORLINE AUTO</h1>
    <div class="person">
      <p class="person__name">Daniel Ravell</p>
      <p class="person__role">Managing Director</p>
    </div>
    <div class="contacts">
      <p class="contact contact--phone">555-555-0148
        <svg viewBox="0 0 24 24"><path d="M6.6 10.8a15.2 15.2 0 0 0 6.6 6.6l2.2-2.2a1 1 0 0 1 1-.25 11.4 11.4 0 0 0 3.6.57 1 1 0 0 1 1 1V20a1 1 0 0 1-1 1A17 17 0 0 1 3 4a1 1 0 0 1 1-1h3.5a1 1 0 0 1 1 1c0 1.25.2 2.45.57 3.6a1 1 0 0 1-.25 1z"/></svg></p>
      <p class="contact contact--phone">555-555-0173
        <svg viewBox="0 0 24 24"><path d="M6.6 10.8a15.2 15.2 0 0 0 6.6 6.6l2.2-2.2a1 1 0 0 1 1-.25 11.4 11.4 0 0 0 3.6.57 1 1 0 0 1 1 1V20a1 1 0 0 1-1 1A17 17 0 0 1 3 4a1 1 0 0 1 1-1h3.5a1 1 0 0 1 1 1c0 1.25.2 2.45.57 3.6a1 1 0 0 1-.25 1z"/></svg></p>
      <p class="contact">www.harborlineautoxq.net
        <svg viewBox="0 0 24 24"><path d="M12 2a10 10 0 1 0 0 20 10 10 0 0 0 0-20zm6.9 6h-3a15.6 15.6 0 0 0-1.3-3.9A8 8 0 0 1 18.9 8zM12 4c.8 1.2 1.5 2.5 1.9 4h-3.8c.4-1.5 1.1-2.8 1.9-4zM4.3 14a8 8 0 0 1 0-4h3.3a16 16 0 0 0 0 4zm.8 2h3a15.6 15.6 0 0 0 1.3 3.9A8 8 0 0 1 5.1 16zm3-8h-3a8 8 0 0 1 4.3-3.9C8.8 5.3 8.4 6.6 8.1 8zM12 20c-.8-1.2-1.5-2.5-1.9-4h3.8c-.4 1.5-1.1 2.8-1.9 4zm2.3-6H9.7a14 14 0 0 1 0-4h4.6a14 14 0 0 1 0 4zm.3 5.9c.6-1.2 1-2.5 1.3-3.9h3a8 8 0 0 1-4.3 3.9zm1.8-5.9a16 16 0 0 0 0-4h3.3a8 8 0 0 1 0 4z"/></svg></p>
      <p class="contact">harborlineautoxq@mailnest.example
        <svg viewBox="0 0 24 24"><path d="M3 5h18a1 1 0 0 1 1 1v12a1 1 0 0 1-1 1H3a1 1 0 0 1-1-1V6a1 1 0 0 1 1-1zm1 2.4V17h16V7.4l-8 5.6z M5 7l7 4.9L19 7z"/></svg></p>
      <p class="contact contact--address">2874 Cresthaven Road, Larkwood Falls, ZZ 00000</p>
    </div>
  </div>
</section>

</body>
</html>
```